Church Website with Home Page and Member Sermon Library

I am in need of an updated design for our church website. This will include 4 pages (outlined below). We are a conservative, evangelical, Christian church. The site should be modern and clean, while still reflecting our conservative values. I already have a logo for our church, and I want the site to incorporate the logo, and match the logo/branding. Stock photos are allowed if needed, but I have uploaded some images of our church and would prefer those images to be used if possible. Any stock photos used should not include any people in the photos (scenery, nature, buildings, animals, etc. are fine).

The site will need 4 pages: Home, Support Us (Donate), Login, and Recording Library.

Page 1: Home
The home page should include the following sections:

- Navigation: Should include links to each section of the home page plus a "listen live" link which will take the user to a live-streaming site and a "support us" link which will take the user to a support/donate page.

- Announcements: Can be either a banner or some other design, but there needs to be some way for us to post announcements for visitors to see. I'm open for creative ideas in this section, but would like it not to take up a lot of room on the page.

- About Us: Should include address, service times (see attached document), and information about the church.

- Pastor Bio: A section that introduces our pastor and gives a short bio about our pastor. Would like this section to include a picture of our pastor. Somewhere in this section I would like to include this Bible reference: "And I will give you pastors according to mine heart, which shall feed you with knowledge and understanding. Jer 3:15 LPW"

- Articles of Faith (What We Believe): This should include several sub-sections each with a heading, body, and possibly 1 or more scripture references. I have attached a document to the brief that includes our articles of faith. Feel free to be creative with this section in how you lay these out and format them.

- Support Us: A small section that explains what kind of support someone can give and a link to a donation page. The link can say something like "Support Us" or "Donate Now".

- Contact form: A contact form that allows the visitor to send us a message. The contact form should ask for name, email, phone, and message.

- Footer: A footer that will be displayed on all pages of the site. This should include at a minimum a link to the home page (or a link to each individual section in the home page if you prefer), a link to "listen live", a link to "support us", a link to "contact us" (or you can put the contact form directly in the footer if you prefer), the address, and a "member login" link.

Page 2: Support Us
The donation page should include a form the visitor can fill out to make a donation. We will embed a third party form later. For this design, please just mock out the design with a basic form asking for name, phone, and email.

Page 3: Login
The recording library (detailed below) will require members to login with a shared numeric code before accessing the page. We need a design for a login screen. The screen should include navigation/footer just like all other pages, but the body of the login page will consist only of a form that asks the user to enter the access code and then a "login" button.

Page 4: Recording Library

The library page is a member-only page that will require a shared, numeric pass code to access. On this page, members will be able to access a filterable list of past sermons. The page by default should display most recent sermons, but should also include a search form that allows the member to filter the sermon list to find a particular sermon. The search form should allow the user to select a filter type (e.g. Speaker name, date, event, etc.) and type in a value to search. They should be able to add multiple filters and remove filters that have been added. Each sermon that is displayed in the result list should include basic information such as title, date, speaker, tags, etc. along with a download icon, and an embedded audio player where they can click a play button to stream it on-demand. Each sermon should also have clickable tags associated with it that can be used to find related sermons.
Updates

I have uploaded several images of our church. Feel free to incorporate these into your design if possible.

Target Market(s)

Church Members

Industry/Entity Type

Religion

Number of Pages Required

4 page

Font styles to use
Sans Serif

Colors

Designer to choose colors to be used in the design.

Requirements
Must have
• Must incorporate the logo (attached)
Nice to have
• Would like the design to incorporate pictures of our church (attached) instead of stock photos if possible.
Should not have
• Please avoid an overly cluttered design. Stock photos used should not include any people in the photos.

```html
<!DOCTYPE html>
<html lang="en">
<head>
<meta charset="utf-8">
<title>Cedar Hill Church</title>
<link rel="stylesheet" href="https://fonts.googleapis.com/css2?family=Marcellus&family=Inter:wght@400;500;600;700&display=swap">
<style>
:root{
  --bg:#e2dcd1;
  --ink:#1b1b1b;
  --text:#2b2b2b;
  --muted:#5a5a5a;
  --green:#628650;
  --green-card:#5e824d;
  --green-dark:#2c4418;
  --teal:#1a8ea6;
  --white:#ffffff;
  --field:#f4f1eb;
}
*{box-sizing:border-box;margin:0;padding:0}
html,body{width:1200px;height:4754px;overflow:hidden}
body{background:var(--bg);font-family:"Inter",sans-serif;color:var(--text);position:relative}
.abs{position:absolute}
.serif{font-family:"Marcellus",serif}
.nav-link{position:absolute;top:44px;font-size:11px;font-weight:700;letter-spacing:.4px;color:var(--ink);text-decoration:none}
.brand{position:absolute;display:flex;align-items:center;justify-content:center;gap:8px;font-family:"Marcellus",serif;color:#3f4d4f;white-space:nowrap}
.brand .mark{display:block;border:1.6px solid #3f4d4f}
.rule{position:absolute;height:2px;background:linear-gradient(90deg,transparent,var(--teal) 20%,var(--teal) 80%,transparent)}
.eyebrow{position:absolute;left:0;width:1200px;text-align:center;font-family:"Marcellus",serif;font-size:11px;letter-spacing:2.5px;color:var(--teal)}
.h2{position:absolute;left:0;width:1200px;text-align:center;font-family:"Marcellus",serif;font-size:35px;color:var(--ink)}
.btn{position:absolute;display:flex;align-items:center;justify-content:center;gap:8px;background:var(--green-dark);color:var(--white);font-size:12px;font-weight:500;border-radius:3px;text-decoration:none;border:0;font-family:"Inter",sans-serif}
.btn.light{background:var(--white);color:var(--ink)}
.btn svg{width:8px;height:8px}
.photo{position:absolute;border-radius:28px;overflow:hidden}
.frame{position:absolute;border-radius:30px;background:var(--teal)}
.h3{position:absolute;font-family:"Marcellus",serif;font-size:29px;line-height:34px;color:var(--ink)}
.para{position:absolute;font-size:14.5px;line-height:21.5px;color:var(--text)}
.time{position:absolute;top:1235px;height:54px;background:#111;border-radius:5px;color:#fff;font-size:11px;font-weight:600;padding:9px 12px;line-height:20px;white-space:nowrap}
.time svg{vertical-align:-3px;margin-right:6px}
.sermon{position:absolute;top:1693px;width:240px;height:351px}
.sermon .avatar{position:absolute;left:55px;top:38px;width:130px;height:130px;border-radius:50%;border:3px solid #fff}
.sermon .title{position:absolute;top:192px;left:28px;right:28px;text-align:center;color:#fff;font-size:12px;font-weight:600;line-height:16px}
.sermon .who{position:absolute;top:232px;width:100%;text-align:center;color:#d9e3d2;font-size:9px}
.sermon .wave{position:absolute;top:262px;left:34px}
.sermon .t{position:absolute;top:298px;color:#e8eee3;font-size:9px}
.art-img{position:absolute;top:3151px;width:258px;height:237px;border-radius:4px}
.art{position:absolute;top:3412px;width:260px;color:#fff}
.art .tag{font-size:8.5px;font-weight:700;letter-spacing:.4px}
.art h4{font-size:17px;font-weight:600;margin-top:9px}
.art p{font-size:10.5px;line-height:17px;margin-top:10px;color:#e9efe4}
.art a{display:block;margin-top:12px;font-size:9.5px;font-weight:700;color:#fff;text-decoration:none}
.contact-form{position:absolute;left:196px;top:4220px;width:808px;height:38px;display:flex;gap:8px}
.contact-form input,.contact-form textarea{flex:1;height:38px;border:1px solid #cfc7b8;background:var(--field);border-radius:3px;padding:0 12px;font:11px "Inter",sans-serif;color:var(--text);resize:none}
.contact-form textarea{flex:1.6;padding-top:12px}
.contact-form .btn{position:static;width:110px;height:38px;flex:none}
.foot-item{position:absolute;top:4503px;font-size:10px;color:#222;white-space:nowrap}
.foot-item.sep{border-left:1px solid #bbb;padding-left:14px}
.foot-item svg{vertical-align:-1px;margin-right:5px}
.social{position:absolute;top:4608px;width:32px;height:32px;border-radius:50%;background:var(--teal)}
</style>
</head>
<body>

<!-- Header -->
<a class="nav-link" style="left:194px">HOME</a>
<a class="nav-link" style="left:260px">ABOUT</a>
<a class="nav-link" style="left:332px">PASTOR</a>
<div class="brand" style="left:500px;top:40px;width:200px;font-size:17px"><span class="mark" style="width:12px;height:12px"></span>Cedar Hill Church</div>
<a class="nav-link" style="left:816px">LIBRARY</a>
<a class="nav-link" style="left:895px">DONATION</a>
<a class="nav-link" style="left:988px">CONTACT</a>
<div class="rule" style="left:130px;top:97px;width:940px"></div>

<!-- Hero -->
<svg class="abs" style="left:44px;top:120px" width="1112" height="609" viewBox="0 0 1112 609" role="img" aria-label="Dim candlelit photo of a cross and hands resting on an open Bible">
  <defs><radialGradient id="heroG" cx="45%" cy="55%" r="70%"><stop offset="0" stop-color="#8a5a2a"/><stop offset=".45" stop-color="#4a2d18"/><stop offset="1" stop-color="#1c130f"/></radialGradient></defs>
  <path d="M0,100 C0,30 40,0 110,5 Q556,40 1002,5 C1072,0 1112,30 1112,100 L1112,509 C1112,579 1072,609 1002,604 Q556,570 110,604 C40,609 0,579 0,509 Z" fill="url(#heroG)"/>
</svg>
<div class="eyebrow" style="top:317px;color:#f1e7da">HOLINESS</div>
<div class="abs serif" style="left:0;width:1200px;top:358px;text-align:center;font-size:45px;line-height:54px;color:#f4ece2">I AM THE WAY, &amp; THE TRUTH<br>AND THE LIFE.</div>
<a class="btn" style="left:541px;top:495px;width:118px;height:35px">Book a Visit <svg viewBox="0 0 8 8"><path d="M2 1l3 3-3 3" fill="none" stroke="#fff" stroke-width="1.4"/></svg></a>

<!-- About -->
<div class="eyebrow" style="top:810px">HOLINESS</div>
<div class="h2" style="top:843px">Know About Cedar Hill Chruch</div>
<div class="frame" style="left:190px;top:950px;width:408px;height:496px"></div>
<div class="photo" style="left:196px;top:942px;width:402px;height:496px;background:linear-gradient(180deg,#5a2a12,#b8621a 45%,#e0a23a 75%,#7a4a22)" role="img" aria-label="Golden interior of the church sanctuary with stained glass windows and altar"></div>
<div class="h3" style="left:665px;top:1022px">Cedar Hill<br>Church Service Time</div>
<div class="para" style="left:665px;top:1110px;width:320px">Printer took a galley of type and scrambled it to make a type specimen book. It has survived not only five centuries, but also the leap into electronic typesetting, remaining essentially unchanged.</div>
<div class="time" style="left:665px;width:144px"><svg width="14" height="14" viewBox="0 0 14 14"><rect x="1.5" y="2.5" width="11" height="10" rx="2" fill="none" stroke="#fff" stroke-width="1.3"/><path d="M1.5 5.5h11M4.5 1v3M9.5 1v3" stroke="#fff" stroke-width="1.3"/></svg>Monday Friday<br>9:00am - 5:30pm PST</div>
<div class="time" style="left:822px;width:155px"><svg width="14" height="14" viewBox="0 0 14 14"><rect x="1.5" y="2.5" width="11" height="10" rx="2" fill="none" stroke="#fff" stroke-width="1.3"/><path d="M1.5 5.5h11M4.5 1v3M9.5 1v3" stroke="#fff" stroke-width="1.3"/></svg>Saturday To Sunday<br>9:00am - 5:30pm PST</div>
<a class="btn" style="left:665px;top:1320px;width:118px;height:40px">Book a Visit <svg viewBox="0 0 8 8"><path d="M2 1l3 3-3 3" fill="none" stroke="#fff" stroke-width="1.4"/></svg></a>

<!-- Sermons -->
<div class="eyebrow" style="top:1585px">HOLINESS</div>
<div class="h2" style="top:1618px">Know About Cedar Hill Chruch</div>

<div class="sermon" style="left:196px">
  <svg class="abs" width="240" height="351" viewBox="0 0 240 351" style="overflow:visible"><rect x="0" y="0" width="240" height="351" rx="120" fill="var(--green-card)"/><g fill="var(--green-card)"><rect x="-8" y="110" width="24" height="12" rx="6"/><rect x="-8" y="138" width="24" height="12" rx="6"/><rect x="-8" y="166" width="24" height="12" rx="6"/><rect x="-8" y="194" width="24" height="12" rx="6"/><rect x="-8" y="222" width="24" height="12" rx="6"/><rect x="224" y="110" width="24" height="12" rx="6"/><rect x="224" y="138" width="24" height="12" rx="6"/><rect x="224" y="166" width="24" height="12" rx="6"/><rect x="224" y="194" width="24" height="12" rx="6"/><rect x="224" y="222" width="24" height="12" rx="6"/></g></svg>
  <div class="avatar" style="background:linear-gradient(160deg,#dfe3e6,#8a7e74)" role="img" aria-label="Portrait of the speaker"></div>
  <div class="title">Simply dummy text of the printing and tyorem</div>
  <div class="who">Ada Morrow</div>
  <svg class="wave" width="172" height="20" viewBox="0 0 172 20"><g fill="#fff"><rect x="0" y="7" width="3" height="6"/><rect x="6" y="5" width="3" height="10"/><rect x="12" y="3" width="3" height="14"/><rect x="18" y="1" width="3" height="18"/><rect x="24" y="4" width="3" height="12"/><rect x="30" y="2" width="3" height="16"/><rect x="36" y="6" width="3" height="8"/><rect x="42" y="3" width="3" height="14"/><rect x="48" y="5" width="3" height="10"/><rect x="54" y="7" width="3" height="6"/></g><g fill="#a9bf9c"><rect x="60" y="4" width="3" height="12"/><rect x="66" y="2" width="3" height="16"/><rect x="72" y="6" width="3" height="8"/><rect x="78" y="3" width="3" height="14"/><rect x="84" y="5" width="3" height="10"/><rect x="90" y="1" width="3" height="18"/><rect x="96" y="4" width="3" height="12"/><rect x="102" y="6" width="3" height="8"/><rect x="108" y="3" width="3" height="14"/><rect x="114" y="5" width="3" height="10"/><rect x="120" y="2" width="3" height="16"/><rect x="126" y="6" width="3" height="8"/><rect x="132" y="4" width="3" height="12"/><rect x="138" y="3" width="3" height="14"/><rect x="144" y="6" width="3" height="8"/><rect x="150" y="4" width="3" height="12"/><rect x="156" y="7" width="3" height="6"/><rect x="162" y="5" width="3" height="10"/></g></svg>
  <div class="t" style="left:52px">24:32</div><div class="t" style="right:52px">34:00</div>
</div>

<div class="sermon" style="left:480px">
  <svg class="abs" width="240" height="351" viewBox="0 0 240 351" style="overflow:visible"><rect x="0" y="0" width="240" height="351" rx="120" fill="var(--green-card)"/><g fill="var(--green-card)"><rect x="-8" y="110" width="24" height="12" rx="6"/><rect x="-8" y="138" width="24" height="12" rx="6"/><rect x="-8" y="166" width="24" height="12" rx="6"/><rect x="-8" y="194" width="24" height="12" rx="6"/><rect x="-8" y="222" width="24" height="12" rx="6"/><rect x="224" y="110" width="24" height="12" rx="6"/><rect x="224" y="138" width="24" height="12" rx="6"/><rect x="224" y="166" width="24" height="12" rx="6"/><rect x="224" y="194" width="24" height="12" rx="6"/><rect x="224" y="222" width="24" height="12" rx="6"/></g></svg>
  <div class="avatar" style="background:linear-gradient(160deg,#3a3a3a,#1a1a1a 60%,#6a4a3a)" role="img" aria-label="Portrait of the speaker at a microphone"></div>
  <div class="title">It is a long established fact that a reader will be</div>
  <div class="who">Ada Morrow</div>
  <svg class="wave" width="172" height="20" viewBox="0 0 172 20"><g fill="#fff"><rect x="0" y="7" width="3" height="6"/><rect x="6" y="5" width="3" height="10"/><rect x="12" y="3" width="3" height="14"/><rect x="18" y="1" width="3" height="18"/><rect x="24" y="4" width="3" height="12"/><rect x="30" y="2" width="3" height="16"/><rect x="36" y="6" width="3" height="8"/><rect x="42" y="3" width="3" height="14"/><rect x="48" y="5" width="3" height="10"/><rect x="54" y="7" width="3" height="6"/></g><g fill="#a9bf9c"><rect x="60" y="4" width="3" height="12"/><rect x="66" y="2" width="3" height="16"/><rect x="72" y="6" width="3" height="8"/><rect x="78" y="3" width="3" height="14"/><rect x="84" y="5" width="3" height="10"/><rect x="90" y="1" width="3" height="18"/><rect x="96" y="4" width="3" height="12"/><rect x="102" y="6" width="3" height="8"/><rect x="108" y="3" width="3" height="14"/><rect x="114" y="5" width="3" height="10"/><rect x="120" y="2" width="3" height="16"/><rect x="126" y="6" width="3" height="8"/><rect x="132" y="4" width="3" height="12"/><rect x="138" y="3" width="3" height="14"/><rect x="144" y="6" width="3" height="8"/><rect x="150" y="4" width="3" height="12"/><rect x="156" y="7" width="3" height="6"/><rect x="162" y="5" width="3" height="10"/></g></svg>
  <div class="t" style="left:52px">24:32</div><div class="t" style="right:52px">34:00</div>
</div>

<div class="sermon" style="left:762px">
  <svg class="abs" width="240" height="351" viewBox="0 0 240 351" style="overflow:visible"><rect x="0" y="0" width="240" height="351" rx="120" fill="var(--green-card)"/><g fill="var(--green-card)"><rect x="-8" y="110" width="24" height="12" rx="6"/><rect x="-8" y="138" width="24" height="12" rx="6"/><rect x="-8" y="166" width="24" height="12" rx="6"/><rect x="-8" y="194" width="24" height="12" rx="6"/><rect x="-8" y="222" width="24" height="12" rx="6"/><rect x="224" y="110" width="24" height="12" rx="6"/><rect x="224" y="138" width="24" height="12" rx="6"/><rect x="224" y="166" width="24" height="12" rx="6"/><rect x="224" y="194" width="24" height="12" rx="6"/><rect x="224" y="222" width="24" height="12" rx="6"/></g></svg>
  <div class="avatar" style="background:linear-gradient(160deg,#4a4440,#242120 60%,#8a8078)" role="img" aria-label="Portrait of the speaker in a studio"></div>
  <div class="title">Contrary to popular belief, Lorem Ipsum is not</div>
  <div class="who">Ada Morrow</div>
  <svg class="wave" width="172" height="20" viewBox="0 0 172 20"><g fill="#fff"><rect x="0" y="7" width="3" height="6"/><rect x="6" y="5" width="3" height="10"/><rect x="12" y="3" width="3" height="14"/><rect x="18" y="1" width="3" height="18"/><rect x="24" y="4" width="3" height="12"/><rect x="30" y="2" width="3" height="16"/><rect x="36" y="6" width="3" height="8"/><rect x="42" y="3" width="3" height="14"/><rect x="48" y="5" width="3" height="10"/><rect x="54" y="7" width="3" height="6"/></g><g fill="#a9bf9c"><rect x="60" y="4" width="3" height="12"/><rect x="66" y="2" width="3" height="16"/><rect x="72" y="6" width="3" height="8"/><rect x="78" y="3" width="3" height="14"/><rect x="84" y="5" width="3" height="10"/><rect x="90" y="1" width="3" height="18"/><rect x="96" y="4" width="3" height="12"/><rect x="102" y="6" width="3" height="8"/><rect x="108" y="3" width="3" height="14"/><rect x="114" y="5" width="3" height="10"/><rect x="120" y="2" width="3" height="16"/><rect x="126" y="6" width="3" height="8"/><rect x="132" y="4" width="3" height="12"/><rect x="138" y="3" width="3" height="14"/><rect x="144" y="6" width="3" height="8"/><rect x="150" y="4" width="3" height="12"/><rect x="156" y="7" width="3" height="6"/><rect x="162" y="5" width="3" height="10"/></g></svg>
  <div class="t" style="left:52px">24:32</div><div class="t" style="right:52px">34:00</div>
</div>

<a class="btn" style="left:535px;top:2086px;width:128px;height:39px">Explore More <svg viewBox="0 0 8 8"><path d="M2 1l3 3-3 3" fill="none" stroke="#fff" stroke-width="1.4"/></svg></a>

<!-- Pastor -->
<div class="h3" style="left:196px;top:2302px">Pastor of Cedar Hill<br>Church</div>
<div class="para" style="left:196px;top:2390px;width:345px">Printer took a galley of type and scrambled it to make a type specimen book. It has survived not only five centuries, but also the leap into electronic typesetting, remaining essentially unchanged.</div>
<div class="para" style="left:196px;top:2519px;width:345px">desktop publishing packages and web page editors now use Lorem Ipsum as their default model text, and a search for 'lorem ipsum' will uncover many web sites still in their infancy. Various versions have evolved over the years, sometimes by.</div>
<a class="btn" style="left:196px;top:2669px;width:118px;height:39px">Book a Visit <svg viewBox="0 0 8 8"><path d="M2 1l3 3-3 3" fill="none" stroke="#fff" stroke-width="1.4"/></svg></a>
<div class="frame" style="left:604px;top:2264px;width:402px;height:496px"></div>
<div class="photo" style="left:596px;top:2256px;width:402px;height:496px;background:linear-gradient(160deg,#d8d2c6,#a89a86 50%,#8a5a30)" role="img" aria-label="Pastor seated in a wooden church pew beside a child"></div>

<!-- Articles of Faith -->
<svg class="abs" style="left:44px;top:2919px" width="1112" height="875" viewBox="0 0 1112 875"><path d="M0,100 C0,30 40,0 110,5 Q556,40 1002,5 C1072,0 1112,30 1112,100 L1112,775 C1112,845 1072,875 1002,870 Q556,836 110,870 C40,875 0,845 0,775 Z" fill="var(--green)"/></svg>
<div class="eyebrow" style="top:3049px;color:#eef2ea">DAILY ARTICLES</div>
<div class="h2" style="top:3078px;color:#fff">Articles of Faith</div>
<div class="art-img" style="left:196px;background:linear-gradient(180deg,#d2c4a8,#7a5a3a 55%,#3a2618)" role="img" aria-label="Gothic church nave with rows of wooden pews"></div>
<div class="art-img" style="left:471px;background:linear-gradient(180deg,#e4dccd,#b89a70 55%,#6a4a30)" role="img" aria-label="Bright cathedral interior with rows of chairs"></div>
<div class="art-img" style="left:746px;background:linear-gradient(180deg,#f1efea,#c8c2b8 50%,#7a5a40)" role="img" aria-label="White chapel with arches and pews leading to the altar"></div>
<div class="art" style="left:204px;width:230px"><div class="tag">EVENTS</div><h4>The God Head</h4><p>We believe in the God head bodily, known as the Divine Trinity. This body consist of God the father, Jesus Christ, his only begotten son and the.</p><a>Know More &#8250;</a></div>
<div class="art" style="left:471px;width:245px"><div class="tag">EVENTS</div><h4>Full Salvation.</h4><p>We believe that Salvation is received only when a person comes to the realization that he or she is lost and separated from God and becomes full of godly sorrow.</p><a>Know More &#8250;</a></div>
<div class="art" style="left:746px;width:255px"><div class="tag">EVENTS</div><h4>Sanctification.</h4><p>Printer took a galley of type and scrambled it to make a type specimen book. It has survived not only five centuries, but also the leap into.</p><a>Know More &#8250;</a></div>
<a class="btn light" style="left:535px;top:3626px;width:128px;height:39px">Explore More <svg viewBox="0 0 8 8"><path d="M2 1l3 3-3 3" fill="none" stroke="#1b1b1b" stroke-width="1.4"/></svg></a>

<!-- Announcements -->
<div class="h2" style="top:3900px">Important Announcement</div>
<div class="abs" style="left:196px;top:3987px;width:406px;height:213px;border-radius:107px;background:var(--green-card)"></div>
<div class="abs" style="left:244px;top:4030px;width:160px;height:130px;border-radius:14px;background:linear-gradient(135deg,#f2a81d,#2a2a2a)" role="img" aria-label="Megaphone illustration with an important announcement banner"></div>
<div class="abs serif" style="left:428px;top:4035px;font-size:32px;line-height:37px;color:#fff">Chruch<br>Closed</div>
<div class="abs" style="left:432px;top:4114px;font-size:10px;line-height:20px;color:#fff"><svg width="14" height="14" viewBox="0 0 14 14" style="vertical-align:-3px;margin-right:6px"><rect x="1.5" y="2.5" width="11" height="10" rx="2" fill="none" stroke="#fff" stroke-width="1.3"/><path d="M1.5 5.5h11" stroke="#fff" stroke-width="1.3"/></svg>Monday Friday<br>9:00am - 5:30pm PST</div>
<div class="abs" style="left:618px;top:3987px;width:386px;height:213px;border-radius:107px;background:#f6f5f2"></div>
<div class="brand" style="left:656px;top:4012px;font-size:11px;gap:5px"><span class="mark" style="width:7px;height:7px;border-width:1px"></span>Cedar Hill Church</div>
<div class="abs" style="left:804px;top:4016px;font-size:13px;color:#222">'Service time Change</div>
<div class="abs" style="left:712px;top:4050px;width:250px;height:110px;border-radius:14px;background:linear-gradient(120deg,#f7c948,#f47b20 60%,#e8e4de)" role="img" aria-label="Service time announcement megaphone illustration"></div>

<!-- Contact form -->
<form class="contact-form" aria-label="Contact us">
  <input type="text" placeholder="Name">
  <input type="email" placeholder="Email">
  <input type="tel" placeholder="Phone">
  <textarea placeholder="Message"></textarea>
  <button class="btn" type="button">Send Message</button>
</form>

<!-- Footer -->
<div class="rule" style="left:196px;top:4279px;width:808px"></div>
<div class="brand" style="left:400px;top:4400px;width:400px;font-size:28px;gap:12px"><span class="mark" style="width:18px;height:18px"></span>Cedar Hill Church</div>
<div class="foot-item" style="left:207px"><svg width="10" height="10" viewBox="0 0 10 10"><path d="M2 1l2 2-1 1.5c.6 1.2 1.3 1.9 2.5 2.5L7 6l2 2-1.5 1.5C4.5 9 1 5.5.5 2.5z" fill="#2c4418"/></svg>+1 55501 23456</div>
<div class="foot-item sep" style="left:314px"><svg width="11" height="9" viewBox="0 0 11 9"><rect x=".5" y=".5" width="10" height="8" fill="none" stroke="#222"/><path d="M.5.5l5 4 5-4" fill="none" stroke="#222"/></svg>hello@cedarhill.org</div>
<div class="foot-item sep" style="left:448px"><svg width="9" height="11" viewBox="0 0 9 11"><path d="M4.5 10.5S.5 6.5.5 4a4 4 0 018 0c0 2.5-4 6.5-4 6.5z" fill="none" stroke="#222"/><circle cx="4.5" cy="4" r="1.3" fill="#222"/></svg>48 Cedar Lane, Springfield</div>
<a class="foot-item sep" style="left:616px;font-weight:700;color:var(--green-dark);text-decoration:none">Listen Live</a>
<a class="foot-item sep" style="left:696px;font-weight:700;color:var(--green-dark);text-decoration:none">Member Login</a>
<a class="btn" style="left:886px;top:4501px;width:118px;height:40px">Book a Visit <svg viewBox="0 0 8 8"><path d="M2 1l3 3-3 3" fill="none" stroke="#fff" stroke-width="1.4"/></svg></a>
<div class="rule" style="left:196px;top:4568px;width:808px"></div>
<div class="social" style="left:514px"></div>
<div class="social" style="left:558px"></div>
<div class="social" style="left:602px"></div>
<div class="social" style="left:648px"></div>
<div class="abs" style="left:0;width:1200px;top:4666px;text-align:center;font-size:10.5px;font-weight:500;color:#222">© Copyright Cedar Hill Church 2023. All Right Reserved.</div>

</body>
</html>
```